larkforge website

commerce website to sell cookeries, brackets, mailboxes and to show off homes built. Modern Steel in design see marlo cycles web page to be like: https://www.marlocycles-demo.com/en/ sorry its bright nest hosting word press divi

must be able to add products to page

Target Market(s)

mainly western states of U.S.

Industry/Entity Type

Building Product

Coding

Coded - Design and coding required

Number of Pages Required

3 page

Font styles to use
Sans Serif

Colors

Designer to choose colors to be used in the design.

Requirements
Must have
• customers to be able to order products from page
• bright nest hosting word press divi

```html
<!DOCTYPE html>
<html lang="en">
<head>
<meta charset="utf-8">
<title>Larkforge</title>
<link href="https://fonts.googleapis.com/css2?family=Arimo:wght@400;500;700&display=swap" rel="stylesheet">
<style>
:root{
  --brand:#46628f;
  --brand-light:#6f8fc0;
  --ink:#2b2b2b;
  --muted:#666666;
  --white:#ffffff;
  --black:#000000;
  --footer:#0e161b;
}
*{margin:0;padding:0;box-sizing:border-box}
html,body{width:1200px;height:2850px;overflow:hidden}
body{font-family:"Arimo",Arial,sans-serif;color:#2b2b2b;background:#ffffff;position:relative;-webkit-font-smoothing:antialiased}
.abs{position:absolute}
a{color:inherit;text-decoration:none}

/* hero */
.hero{left:0;top:0;width:1200px;height:534px;background:linear-gradient(120deg,#2c3a2e 0%,#1c2824 35%,#2e3330 60%,#55574f 78%,#1e2624 100%)}
.hero-shade{left:0;top:0;width:1200px;height:534px;background:linear-gradient(180deg,rgba(0,0,0,.15) 0%,rgba(0,0,0,.35) 100%)}
.brand-name{font-weight:500;font-size:20px;letter-spacing:1px;color:#ffffff;display:flex;align-items:center;gap:8px}
.brand-dot{width:14px;height:14px;border-radius:50%;background:currentColor}
.site-brand{left:110px;top:48px}
.nav{top:39px;font-size:13.5px;font-weight:700;color:#ffffff;letter-spacing:.2px}
.nav.active{color:var(--brand-light)}
.nav.active::after{content:"";position:absolute;left:0;right:0;top:20px;height:2px;background:var(--brand-light)}
.cart{left:988px;top:30px;width:109px;height:33px;border:1px solid var(--brand-light);display:flex;align-items:center;justify-content:center;gap:10px;color:#ffffff;font-size:10.5px;font-weight:700}
.cart-badge{position:absolute;left:31px;top:3px;width:11px;height:11px;border-radius:50%;background:#e04848;font-size:7px;text-align:center;line-height:11px}
.hero-title{left:0;width:1168px;top:196px;text-align:center;font-size:42px;font-weight:700;color:#ffffff;letter-spacing:.3px}
.hero-copy{left:293px;width:595px;top:262px;font-size:17px;line-height:19.5px;color:#ffffff;text-align:center}
.btn{background:var(--brand);color:#ffffff;display:flex;align-items:center;justify-content:center;font-size:20px}
.hero-btn{left:477px;top:381px;width:214px;height:54px}
.dots{left:538px;top:483px;display:flex;gap:10px;align-items:center}
.dots span{width:9px;height:9px;border-radius:50%;background:#ffffff}
.dots span.on{width:14px;height:14px;background:var(--brand);border:3px solid #ffffff}

/* about */
.about-photo{left:140px;top:609px;width:503px;height:382px;background:linear-gradient(160deg,#5a4656 0%,#8e8088 30%,#cfcbcc 50%,#6a5664 70%,#2a1e28 100%)}
.about-title{right:112px;top:632px;font-size:28px;font-weight:700;color:#2b2b2b}
.about-rule{left:948px;top:667px;width:140px;height:4px;background:var(--brand)}
.about-lead{left:660px;width:428px;top:701px;font-size:16px;line-height:19px;text-align:right;color:#1a1a1a}
.about-body{left:680px;width:408px;top:768px;font-size:13.5px;line-height:19.2px;color:#666666;text-align:right}
.about-btn{left:874px;top:910px;width:214px;height:54px}

/* manufacture */
.mf-band{left:0;top:1089px;width:1200px;height:671px;background:linear-gradient(100deg,#3a3028 0%,#101820 40%,#3a2414 55%,#1a2430 80%,#3c4756 100%)}
.panel{background:#ffffff}
.thumb{background:linear-gradient(180deg,#ffffff 0%,#3a3a3a 30%,#1c1c1c 65%,#f2f2f2 100%)}
.cat-title{font-size:17.5px;color:#2b2b2b;text-align:center}
.cat-copy{font-size:11px;line-height:15.5px;color:#666666;text-align:center}
.mf-box{left:471px;top:1386px;width:261px;height:254px;background:var(--brand);color:#ffffff}
.mf-title{left:0;width:261px;top:27px;text-align:center;font-size:28px;font-weight:700}
.mf-copy{left:29px;width:206px;top:79px;font-size:11px;line-height:15.5px;font-weight:700;text-align:left;color:#ffffff}
.mf-btn{left:29px;top:168px;width:201px;height:49px;border:1.5px solid #ffffff;display:flex;align-items:center;justify-content:center;font-size:20px}

/* products */
.products-title{left:110px;top:1805px;font-size:27px;font-weight:700;color:#2b2b2b}
.products-copy{left:110px;top:1853px;width:820px;font-size:13.5px;line-height:16px;color:#666666}
.shop-title{left:159px;top:1929px;font-size:26px;font-weight:400;color:#777777}
.results{left:159px;top:1990px;font-size:12.5px;color:#666666}
.sort{left:893px;top:1984px;width:177px;height:34px;border:1px solid #aaaaaa;font-size:12.5px;color:#666666;display:flex;align-items:center;padding-left:9px;gap:4px}
.product-img{background:linear-gradient(180deg,#ffffff 0%,#2e2e2e 25%,#161616 60%,#bdbdbd 85%,#ffffff 100%)}
.sale{width:40px;height:40px;border-radius:50%;background:#111111;color:#ffffff;font-size:13px;display:flex;align-items:center;justify-content:center}
.p-name{font-size:13.5px;color:#666666}
.p-price{font-size:11px;color:#222222}
.p-price s{color:#666666}
.add-btn{width:135px;height:31px;background:#000000;color:#ffffff;font-size:12px;display:flex;align-items:center;justify-content:center}
.arrow{width:30px;height:31px;background:#000000;display:flex;align-items:center;justify-content:center}

/* footer */
.footer{left:0;top:2527px;width:1200px;height:323px;background:var(--footer);color:#ffffff}
.footer .brand-name{color:var(--brand-light);font-size:21px}
.foot-line{font-size:16px;line-height:19.5px;display:flex;gap:12px;align-items:flex-start;color:#ffffff}
.foot-head{font-size:17px;color:var(--brand-light);letter-spacing:.3px}
.foot-links{font-size:16.5px;line-height:32px;color:#ffffff}
.copyright{left:0;width:1106px;text-align:center;top:299px;font-size:11px;color:#ffffff}
</style>
</head>
<body>

<!-- hero -->
<section class="abs hero" role="img" aria-label="Photo of a hand lifting the vented lid of a charcoal kettle grill"></section>
<div class="abs hero-shade"></div>
<div class="abs site-brand brand-name"><span class="brand-dot"></span>LARKFORGE</div>
<a class="abs nav active" style="left:403px">HOME</a>
<a class="abs nav" style="left:492px">ABOUT US</a>
<a class="abs nav" style="left:610px">PRODUCT</a>
<a class="abs nav" style="left:727px">MANUFACTURE</a>
<a class="abs nav" style="left:880px">CONTACTS</a>
<a class="abs cart">
  <svg width="20" height="16" viewBox="0 0 20 16"><path d="M1 2h3l2 9h10l2-7H5" fill="none" stroke="#fff" stroke-width="1.5"/><circle cx="8" cy="14" r="1.4" fill="#fff"/><circle cx="15" cy="14" r="1.4" fill="#fff"/></svg>
  <span class="cart-badge">2</span>
  My Cart
</a>
<h1 class="abs hero-title">CONSECTETUR ADIPISCING</h1>
<p class="abs hero-copy">Lorem ipsum dolor sit amet, consectetur adipiscing elit, sed do eiusmod tempor incididunt ut labore et dolore magna aliqua. Quis ipsum suspendisse ultrices gravida. Risus commodo viverra maecenas accumsan lacus vel facilisis.</p>
<a class="abs btn hero-btn">Our Services</a>
<div class="abs dots"><span></span><span></span><span class="on"></span><span></span></div>

<!-- about -->
<div class="abs about-photo" role="img" aria-label="Photo of meat smoking on a charcoal grill outdoors"></div>
<h2 class="abs about-title">ABOUT US</h2>
<div class="abs about-rule"></div>
<p class="abs about-lead">Lorem ipsum dolor sit amet, consectetur adipiscing elit, sed do eiusmod tempor incididunt</p>
<p class="abs about-body">ut labore et ultrices gravida. Risus commodo viverra maecenas accumsan lacus dolore magna aliqua. Quis ipsum suspendisse ultrices ut labore et dolore magna aliqua. Quis ipsum suspendisse ultrices gravida. Risus commodo viverra maecenas accumsan lacus vel facilisis.</p>
<a class="abs btn about-btn">Read More</a>

<!-- manufacture -->
<section class="abs mf-band" role="img" aria-label="Photo of a burger patty over grill flames"></section>
<div class="abs panel" style="left:175px;top:1161px;width:296px;height:479px"></div>
<div class="abs panel" style="left:0;top:1445px;width:471px;height:195px"></div>
<div class="abs panel" style="left:732px;top:1161px;width:289px;height:479px"></div>
<div class="abs panel" style="left:732px;top:1444px;width:468px;height:194px"></div>

<div class="abs thumb" style="left:260px;top:1176px;width:133px;height:118px" role="img" aria-label="Product photo of assorted portable grills"></div>
<div class="abs cat-title" style="left:175px;width:290px;top:1303px">Cooking Equipmebnts</div>
<p class="abs cat-copy" style="left:206px;width:242px;top:1326px">ut labore et ultrices gravida. Risus commodo viverra maecenas accumsan lacus dolore magna aliqua. Quis ipsum suspendis</p>

<div class="abs thumb" style="left:265px;top:1405px;width:155px;height:210px" role="img" aria-label="Product photo of a round charcoal grill on legs"></div>
<div class="abs cat-title" style="left:0;width:246px;top:1485px">Preparation Equipmebnts</div>
<p class="abs cat-copy" style="left:8px;width:242px;top:1517px">ut labore et ultrices gravida. Risus commodo viverra maecenas accumsan lacus dolore magna aliqua. Quis ipsum suspendis</p>

<div class="abs thumb" style="left:813px;top:1169px;width:110px;height:125px" role="img" aria-label="Product photo of a gas grill with side shelves"></div>
<div class="abs cat-title" style="left:732px;width:275px;top:1304px">Bar Equipmebnts</div>
<p class="abs cat-copy" style="left:756px;width:242px;top:1326px">ut labore et ultrices gravida. Risus commodo viverra maecenas accumsan lacus dolore magna aliqua. Quis ipsum suspendis</p>

<div class="abs thumb" style="left:787px;top:1401px;width:153px;height:208px" role="img" aria-label="Product photo of a kettle grill on wheels"></div>
<div class="abs cat-title" style="left:940px;width:240px;top:1485px">Outdoor Equipmebnts</div>
<p class="abs cat-copy" style="left:947px;width:242px;top:1517px">ut labore et ultrices gravida. Risus commodo viverra maecenas accumsan lacus dolore magna aliqua. Quis ipsum suspendis</p>

<div class="abs mf-box">
  <h2 class="abs mf-title">MANUFACTURE</h2>
  <p class="abs mf-copy">ut labore et ultrices gravida. Risus commodo viverra maecenas accumsan lacus dolore magna aliqua. Quis ipsum suspendis magna aliqua. Quis ipsum su</p>
  <a class="abs mf-btn">View More</a>
</div>

<!-- products -->
<h2 class="abs products-title">PRODUCTS</h2>
<p class="abs products-copy">Lorem ipsum dolor sit amet, consectetur adipiscing elit, sed do eiusmod tempor incididunt ut labore et dolore magna aliqua. Quis ipsum suspendisse ultrices gravida. Risus commodo viverra maecenas accumsan lacus vel facilisis.</p>
<h3 class="abs shop-title">Shop</h3>
<div class="abs results">showing 1-30 of 32 results</div>
<div class="abs sort">Sort by price: high to low
  <svg width="8" height="6" viewBox="0 0 8 6"><path d="M1 1l3 3 3-3" fill="none" stroke="#555" stroke-width="1.5"/></svg>
</div>

<div class="abs product-img" style="left:160px;top:2068px;width:205px;height:255px" role="img" aria-label="Product photo of a kettle grill on wheels"></div>
<div class="abs sale" style="left:418px;top:2043px">sale!</div>
<div class="abs p-name" style="left:164px;top:2353px">Master Package Outdoor</div>
<div class="abs p-price" style="left:160px;top:2377px"><s>$ 1,457.00</s> $999.00</div>
<a class="abs add-btn" style="left:163px;top:2402px">Add to cart</a>

<div class="abs product-img" style="left:462px;top:2075px;width:210px;height:245px" role="img" aria-label="Product photo of a gas grill with side shelves"></div>
<div class="abs sale" style="left:726px;top:2043px">sale!</div>
<div class="abs p-name" style="left:471px;top:2353px">Master Package Outdoor</div>
<div class="abs p-price" style="left:467px;top:2377px"><s>$ 1,457.00</s> $999.00</div>
<a class="abs add-btn" style="left:470px;top:2402px">Add to cart</a>

<div class="abs product-img" style="left:774px;top:2085px;width:210px;height:225px" role="img" aria-label="Product photo of a round charcoal grill on legs"></div>
<div class="abs sale" style="left:1033px;top:2043px">sale!</div>
<div class="abs p-name" style="left:778px;top:2353px">Master Package Outdoor</div>
<div class="abs p-price" style="left:774px;top:2377px"><s>$ 1,457.00</s> $999.00</div>
<a class="abs add-btn" style="left:777px;top:2402px">Add to cart</a>

<a class="abs arrow" style="left:1002px;top:2451px"><svg width="10" height="16" viewBox="0 0 10 16"><path d="M8 2L3 8l5 6" fill="none" stroke="#fff" stroke-width="2.5"/></svg></a>
<a class="abs arrow" style="left:1052px;top:2451px"><svg width="10" height="16" viewBox="0 0 10 16"><path d="M2 2l5 6-5 6" fill="none" stroke="#fff" stroke-width="2.5"/></svg></a>

<!-- footer -->
<footer class="abs footer">
  <div class="abs brand-name" style="left:127px;top:46px"><span class="brand-dot"></span>LARKFORGE</div>
  <div class="abs foot-line" style="left:97px;top:124px">
    <svg width="14" height="17" viewBox="0 0 14 17"><path d="M7 16s5.5-5.5 5.5-9.5a5.5 5.5 0 0 0-11 0C1.5 10.5 7 16 7 16z" fill="none" stroke="#fff" stroke-width="1.3"/><circle cx="7" cy="6.5" r="2" fill="none" stroke="#fff" stroke-width="1.3"/></svg>
    <span>Larkforge, No.18 Harlow Lane, Cedar<br>Flats, Oregon, USA 970 214</span>
  </div>
  <div class="abs foot-line" style="left:97px;top:192px">
    <svg width="14" height="14" viewBox="0 0 14 14"><path d="M3 1l2.5 3-1.5 2c1 2 2 3 4 4l2-1.5 3 2.5-1.5 2C6 13 1 8 1 2.5z" fill="#fff"/></svg>
    <span>+1 555 210 4839</span>
  </div>
  <div class="abs foot-line" style="left:97px;top:240px">
    <svg width="14" height="12" viewBox="0 0 14 12"><rect x="1" y="1.5" width="12" height="9" fill="none" stroke="#fff" stroke-width="1.2"/><path d="M1 2l6 5 6-5" fill="none" stroke="#fff" stroke-width="1.2"/></svg>
    <span>hello@larkforge-demo.com</span>
  </div>
  <div class="abs foot-head" style="left:531px;top:63px">INFORMATION</div>
  <div class="abs foot-links" style="left:532px;top:101px">home<br>about us<br>product<br>manufacture<br>contacts</div>
  <div class="abs foot-head" style="left:834px;top:63px">HELP &amp; SUPPORT</div>
  <div class="abs foot-links" style="left:834px;top:101px">contacts<br>my account<br>cart</div>
  <div class="abs copyright">© Copyright 2020. All rights reserved.</div>
</footer>

</body>
</html>
```